Quorva - corporate Business Card

We need a good look and innovative business card for a new start up company based in Los Angeles called "Quorva". We are in a payment business, including payment card, app, and ewallet. We are expert in online payment and Card not present (CNP) transaction.
We need an innovative, modern business card.

Our logo font is Aero Matics

Target Market(s)

Startup - Bank - Online Payment - Card Manufacturing

Industry/Entity Type

Startup

Contact Information for Business Card

phone: 555 014 7396 - Address: 4172 Marlowe blvd, Brenmoor Vale, NV 90299

Requirements
Must have
• Message: innovative, professional, expert, high tech, trust, online payment expert, security
Nice to have
• no comment
Should not have
• no Comment

```html
<!DOCTYPE html>
<html lang="en">
<head>
<meta charset="utf-8">
<title>Quorva – Business Card</title>
<link href="https://fonts.googleapis.com/css2?family=Source+Sans+3:wght@400;600;700&display=swap" rel="stylesheet">
<style>
  :root {
    --stage-top: #646464;
    --stage-bottom: #727272;
    --brand-red: #b71c2e;
    --brand-red-soft: #bf2a3b;
    --paper: #ffffff;
    --emboss-light: rgba(255,255,255,0.10);
    --emboss-dark: rgba(0,0,0,0.12);
  }
  * { margin: 0; padding: 0; box-sizing: border-box; }
  html, body { width: 1200px; height: 900px; overflow: hidden; }
  body {
    background: linear-gradient(180deg, var(--stage-top), var(--stage-bottom));
    font-family: "Source Sans 3", "Myriad Pro", Arial, sans-serif;
    position: relative;
  }
  .card {
    position: absolute;
    top: 306px;
    height: 271px;
    border-radius: 10px;
    overflow: hidden;
    box-shadow: 0 1px 3px rgba(0,0,0,0.25);
  }
  /* Front */
  .card-front { left: 149px; width: 439px; background: var(--brand-red); }
  .front-header {
    position: absolute; left: 0; top: 0; width: 100%; height: 118px;
    background: var(--paper);
  }
  .front-wordmark {
    position: absolute; left: 22px; top: 16px;
    font-weight: 600; font-size: 74px; line-height: 1;
    color: var(--brand-red); letter-spacing: 1px;
  }
  .emboss-circle {
    position: absolute; left: 282px; top: 127px;
    width: 140px; height: 140px; border-radius: 50%;
    border: 2px solid var(--emboss-dark);
    box-shadow: inset 1px 1px 0 var(--emboss-light), 1px 1px 0 var(--emboss-light);
  }
  .holder { position: absolute; left: 23px; top: 153px; color: var(--paper); }
  .holder-name { font-weight: 700; font-size: 15px; letter-spacing: 0.3px; line-height: 1; }
  .holder-title { font-size: 12.5px; line-height: 1; margin-top: 3px; }
  .contact-list {
    position: absolute; left: 23px; top: 197px; list-style: none;
    color: var(--paper); font-size: 12.5px;
  }
  .contact-list li { display: flex; align-items: center; height: 17px; white-space: nowrap; }
  .contact-list svg { width: 10px; height: 11px; margin-right: 6px; fill: var(--paper); flex: none; }
  /* Back */
  .card-back { left: 608px; width: 441px; }
  .back-pattern {
    position: absolute; inset: 0;
    background: radial-gradient(circle at 50% 50%, var(--brand-red-soft), var(--brand-red) 80%);
  }
  .back-mark {
    position: absolute; left: 80px; top: 93px;
    width: 86px; height: 86px; border-radius: 50%;
    background: var(--paper);
  }
  .back-wordmark {
    position: absolute; left: 174px; top: 104px;
    font-weight: 600; font-size: 58px; line-height: 1;
    color: var(--paper); letter-spacing: 1px;
  }
  .back-web {
    position: absolute; left: 0; width: 441px; top: 224px;
    text-align: center; color: var(--paper); font-size: 12.5px;
  }
</style>
</head>
<body>
  <section class="card card-front">
    <div class="front-header">
      <div class="front-wordmark">quorva</div>
    </div>
    <div class="emboss-circle"></div>
    <div class="holder">
      <div class="holder-name">DANIEL REYES</div>
      <div class="holder-title">Managing Director</div>
    </div>
    <ul class="contact-list">
      <li><svg viewBox="0 0 10 10"><path d="M2 0.5 L3.6 2.6 L2.6 3.6 Q3.6 5.8 6.4 7.4 L7.4 6.4 L9.5 8 L8.3 9.5 Q4.5 9.3 1.6 5.8 Q0.3 3.8 0.5 1.7 Z"/></svg>555 014 7396</li>
      <li><svg viewBox="0 0 10 10"><circle cx="5" cy="5" r="4.6"/><path d="M1 5 H9 M5 0.6 Q2.6 5 5 9.4 M5 0.6 Q7.4 5 5 9.4" stroke="#b71c2e" stroke-width="0.7" fill="none"/></svg>www.quorva.com</li>
      <li><svg viewBox="0 0 10 12"><path d="M5 0.3 A4.3 4.3 0 0 1 9.3 4.6 Q9.3 7.2 5 11.7 Q0.7 7.2 0.7 4.6 A4.3 4.3 0 0 1 5 0.3 Z"/><circle cx="5" cy="4.6" r="1.7" fill="#b71c2e"/></svg>4172 Marlowe blvd, Brenmoor Vale, NV 90299</li>
    </ul>
  </section>

  <section class="card card-back">
    <div class="back-pattern" role="img" aria-label="Repeating faint brand-circle pattern across the red card back"></div>
    <div class="back-mark"></div>
    <div class="back-wordmark">quorva</div>
    <div class="back-web">www.quorva.com</div>
  </section>
</body>
</html>
```